Fun relaxed Travel Photography Business Card*

Require a fun, funky and quirky but rememberable business card for a travel photographer

Industry/Entity Type

Photographer

Contact Information for Business Card

Front Card

(my name) Lenn D.

Travel Photographer ( small under travel photographer) “self-proclaimed”

(website logo) wanderingsoflenn.net

(Instagram logo) @wanderings_of_lenn

(Instagram logo) @wanderings_of_lenn_2.0 (backup for when Instagram puts Lenn on timeout for bad behaviour)

Tel: N/A (removing the potential awkwardness of me not replying)

Email: (see above)

Back Card

Offending people since 1986

(Bottom right corner) “p.s. travelling made me fatTER”

Font styles to use
Serif

Colors

Designer to choose colors to be used in the design.

Requirements
Must have
• a camera
• a similar cartoon version of me as the "logo" see attached files, try to make as similar as possible

```html
<!DOCTYPE html>
<html lang="en">
<head>
<meta charset="utf-8">
<title>Lenn D. — Travel Photographer Business Card</title>
<link href="https://fonts.googleapis.com/css2?family=Lato:wght@300;400;700&display=swap" rel="stylesheet">
<style>
  :root {
    --backdrop: #8e5327;
    --card-dark: #121212;
    --card-light: #e6e6e6;
    --pattern-tone: #d2d2d2;
    --ink-light: #ffffff;
    --ink-soft: #d9d9d9;
    --ink-dark: #141414;
    --rule: #8a8a8a;
  }
  * { margin: 0; padding: 0; box-sizing: border-box; }
  html, body { width: 1200px; height: 900px; overflow: hidden; }
  body {
    background: var(--backdrop);
    font-family: "Lato", sans-serif;
    position: relative;
  }
  .card {
    position: absolute;
    box-shadow: 3px 4px 6px rgba(0,0,0,0.45);
    overflow: hidden;
  }
  /* Front */
  .card-front {
    left: 330px; top: 90px; width: 555px; height: 345px;
    background: var(--card-dark);
    color: var(--ink-light);
    text-align: center;
  }
  .brand-name {
    position: absolute; left: 0; right: 0; top: 42px;
    font-size: 58px; font-weight: 300; line-height: 1;
    letter-spacing: 1px;
  }
  .brand-title {
    position: absolute; left: 0; right: 0; top: 114px;
    font-size: 13px; font-weight: 700; letter-spacing: 1.2px;
  }
  .divider {
    position: absolute; left: 178px; width: 178px; height: 20px;
    display: flex; align-items: center; gap: 4px;
  }
  .divider::before, .divider::after {
    content: ""; flex: 1; height: 1px; background: var(--rule);
  }
  .divider-contact { top: 148px; }
  .divider-social { top: 248px; }
  .icon { width: 20px; height: 20px; display: block; }
  .contact-list {
    position: absolute; left: 0; right: 0; top: 181px;
    list-style: none; font-size: 16px; line-height: 20px;
  }
  .social-list {
    position: absolute; left: 0; right: 0; top: 274px;
    list-style: none; font-size: 16px; line-height: 20px;
    color: var(--ink-soft);
  }
  /* Back */
  .card-back {
    left: 330px; top: 468px; width: 558px; height: 344px;
    background: var(--card-light);
    color: var(--ink-dark);
  }
  .pattern-fill {
    position: absolute; inset: 0;
    background: linear-gradient(180deg, var(--pattern-tone), #dcdcdc 50%, var(--pattern-tone));
  }
  .back-logo {
    position: absolute; left: 0; right: 0; top: 118px;
    text-align: center;
  }
  .back-name {
    display: inline-flex; align-items: center; gap: 12px;
    font-size: 58px; font-weight: 300; line-height: 1;
  }
  .back-name .mark-square {
    width: 40px; height: 40px; border: 3px solid var(--ink-dark);
  }
  .back-title {
    margin-top: 6px; font-size: 13px; font-weight: 700; letter-spacing: 1.2px;
  }
  .back-subtitle {
    display: inline-block; margin-top: 2px;
    font-size: 8px; font-weight: 700; letter-spacing: 1px;
    padding: 0 6px 2px; border-bottom: 2px solid var(--ink-dark);
  }
  .tagline-band {
    position: absolute; left: 0; right: 0; top: 290px; height: 33px;
    background: #0c0c0c; color: var(--ink-light);
    font-size: 14.5px; letter-spacing: 0.3px;
    display: flex; align-items: center;
  }
  .tagline-band span:first-child { margin-left: 31px; }
  .tagline-band span:last-child { margin-left: auto; margin-right: 38px; }
</style>
</head>
<body>

<section class="card card-front" aria-label="Business card front">
  <h1 class="brand-name">Lenn D</h1>
  <p class="brand-title">TRAVEL PHOTOGRAPHER</p>

  <div class="divider divider-contact">
    <svg class="icon" viewBox="0 0 20 20" aria-label="Phone"><circle cx="10" cy="10" r="10" fill="#fff"/><path d="M6 7c0-1 1-1.6 2-1.6h4c1 0 2 .6 2 1.6v1h-2V7H8v1H6z M7 9h6l1 5H6z" fill="#121212"/></svg>
    <svg class="icon" viewBox="0 0 20 20" aria-label="Email"><circle cx="10" cy="10" r="10" fill="#fff"/><rect x="5" y="6.5" width="10" height="7" fill="none" stroke="#121212" stroke-width="1.3"/><path d="M5 6.5l5 4 5-4" fill="none" stroke="#121212" stroke-width="1.3"/></svg>
    <svg class="icon" viewBox="0 0 20 20" aria-label="Website"><circle cx="10" cy="10" r="10" fill="#fff"/><circle cx="10" cy="10" r="5.5" fill="none" stroke="#121212" stroke-width="1.3"/><path d="M4.5 10h11M10 4.5c-2.5 3-2.5 8 0 11M10 4.5c2.5 3 2.5 8 0 11" fill="none" stroke="#121212" stroke-width="1"/></svg>
  </div>

  <ul class="contact-list">
    <li>555 0142 7788</li>
    <li>info@wanderingsoflenn.net</li>
    <li>www.wanderingsoflenn.net</li>
  </ul>

  <div class="divider divider-social">
    <svg class="icon" viewBox="0 0 20 20" aria-label="Social handles"><circle cx="10" cy="10" r="10" fill="#fff"/></svg>
  </div>

  <ul class="social-list">
    <li>@wanderings_of_lenn</li>
    <li>@wanderings_of_lenn_2.0</li>
  </ul>
</section>

<section class="card card-back" aria-label="Business card back">
  <div class="pattern-fill" role="img" aria-label="Light grey repeating pattern of cameras, film reels, lenses and a camera operator"></div>

  <div class="back-logo">
    <div class="back-name"><span class="mark-square"></span>Lenn D</div>
    <p class="back-title">TRAVEL PHOTOGRAPHER</p>
    <span class="back-subtitle">SELF-PROCLAIMED</span>
  </div>

  <div class="tagline-band">
    <span>OFFENDING PEOPLE SINCE 1986</span>
    <span>P.S. TRAVELLING MADE ME FATTER</span>
  </div>
</section>

</body>
</html>
```